CoinHarbor.com Site Redesign

We are looking to redesign our CoinHarbor.com site. This site is focused on helping consumers make smart financial decisions. We provide reviews and articles in various categories.

We are looking for a responsive design to run on wordpress. We will also have adsense advertisements on our page and will want some ad spot space. We are thinking of two column design vs. single column.

Here is an example of what our competitors look like:
ShopperBeacon.org (mostly reviews vs. articles)
Homepage - https://www.shopperbeacon.example/
Category Review Listing - https://www.shopperbeacon.example/mortgage-refinance/best-mortgage-refinance
Individual Review - https://www.shopperbeacon.example/mortgage-refinance/c/loan-orchard-mortgage-refinance-review

- I like that the site is extremely clean. I like the fixed header in mobile

PilotGuide
Homepage - https://www.pilotguide.example/
Category Review Listing-https://www.pilotguide.example/auto_insurance/index.php
Individual Review- https://www.pilotguide.example/auto_insurance/drivora_review.php

Articles - https://www.pilotguide.example/blog/2017/11/20/going-on-a-holiday-road-trip-be-prepared-for-these-hazards/

What I Like? I like the two column layout in that it gives room for advertising.
What I Do NOT Like? The top navigation is a little cumbersome and old. Mobile view is not very good. Content seems a bit cluttered.

PennyMoth
Homepage - https://www.pennymoth.example
Category Review Listing - https://www.pennymoth.example/blog/insurance/best-car-insurance-companies/?trk=pm_gn1_4.0
Individual Review- https://www.pennymoth.example/blog/insurance/veloro-insurance-review/

What I Like? very clean. Like the use of white space and focus on bright color call to action buttons.
What I Do NOT Like? In mobile a lot of content is pushed below the fold because of the large image above the fold. Reviews are not well organized.

Target Market(s)

consumers interested in saving money and making smart financial decisions

Industry/Entity Type

Financial

Logo Text

CoinHarbor.com or CoinHarbor

Coding

Coded - Design and coding required

Number of Pages Required

5+ page

Font styles to use
Sans Serif

Colors

Designer to choose colors to be used in the design.

Requirements
Must have
• -responsive design
• -room for ad space in the right column
Nice to have
• -good use of white space
• -clean layouts
Should not have
• -clutter

```html
<!DOCTYPE html>
<html lang="en">
<head>
<meta charset="utf-8">
<title>CoinHarbor.com – Make Smarter Financial Decisions</title>
<link href="https://fonts.googleapis.com/css2?family=Montserrat:wght@400;500;600;700&family=Arimo:wght@400;700&display=swap" rel="stylesheet">
<style>
:root{
  --navy:#0f2f80;
  --navy-deep:#0b2a72;
  --blue:#1f7fc4;
  --text:#444;
  --muted:#666;
  --line:#e3e3e3;
  --footer-bg:#f2f2f2;
  --white:#fff;
}
*{margin:0;padding:0;box-sizing:border-box}
html,body{width:1200px;height:2782px;overflow:hidden;background:var(--white)}
body{position:relative;font-family:"Arimo",Arial,sans-serif;color:var(--text)}
.abs{position:absolute}
h1,h2,h3,h4,.nav a,.tile-label{font-family:"Montserrat",Arial,sans-serif}

/* header */
.site-header{left:0;top:0;width:1200px;height:96px;background:var(--white)}
.brand{left:85px;top:30px;display:flex;align-items:center;gap:8px;font:700 21px "Montserrat",sans-serif;color:var(--navy)}
.brand-mark{width:30px;height:30px;background:var(--navy)}
.nav{left:370px;top:42px;width:690px;height:16px}
.nav a{position:absolute;white-space:nowrap;font-size:11px;font-weight:600;color:#333;text-decoration:none;top:0}
.nav a.active{color:var(--blue)}
.search-btn{left:1071px;top:26px;width:44px;height:44px;border-radius:50%;background:var(--navy)}

/* hero */
.hero{left:0;top:96px;width:1200px;height:509px;background:linear-gradient(120deg,#3b4a58 0%,#6d7882 40%,#8d949b 60%,#3e4a5a 100%)}
.hero-shade{left:0;top:96px;width:1200px;height:509px;background:rgba(20,25,35,.35)}
.hero-title{left:0;top:288px;width:1200px;text-align:center;color:var(--white);font-size:32px;font-weight:700;letter-spacing:.5px}
.hero-sub{left:0;top:336px;width:1200px;text-align:center;color:var(--white);font:500 20px "Montserrat",sans-serif;letter-spacing:.5px}
.hero-search{left:226px;top:390px;width:748px;height:46px;border-radius:23px;background:var(--white);overflow:hidden}
.hero-search span{position:absolute;left:26px;top:15px;font-size:13px;color:#555}
.hero-search b{position:absolute;right:0;top:0;width:113px;height:46px;background:var(--blue);color:var(--white);font:600 16px "Montserrat",sans-serif;text-align:center;line-height:46px;letter-spacing:.5px}

/* welcome */
.welcome-title{left:0;top:651px;width:1200px;text-align:center;color:var(--navy);font-size:23px;font-weight:600}
.welcome-text{left:0;top:692px;width:1200px;text-align:center;font-size:13px;color:#333}

/* category grid */
.tile{overflow:hidden}
.tile-label{position:absolute;left:50%;transform:translateX(-50%);bottom:24px;background:rgba(255,255,255,.85);color:#333;font-size:14px;font-weight:600;white-space:nowrap;padding:13px 20px;letter-spacing:.3px}
.tile-feature{background:linear-gradient(135deg,#1f5fb0,#2d78c6 60%,#1a4f98)}
.feature-title{position:absolute;left:0;top:82px;width:100%;text-align:center;color:var(--white);font:700 18px "Montserrat",sans-serif}
.feature-text{position:absolute;left:100px;top:125px;width:386px;text-align:center;color:var(--white);font-size:13px;line-height:26px}

/* ad banner */
.ad-banner{left:289px;top:1510px;width:624px;height:78px;border:1px solid #999;background:linear-gradient(90deg,#dfe9f2,#ffffff 55%,#e6eef5);overflow:hidden}
.ad-banner .ad-head{position:absolute;left:72px;top:20px;font:700 17px "Montserrat",sans-serif;color:var(--navy);white-space:nowrap}
.ad-banner .ad-sub{position:absolute;left:72px;top:44px;font-size:14px;color:#333}
.ad-banner .ad-car{position:absolute;left:345px;top:12px;width:100px;height:52px;background:linear-gradient(#3a5fa8,#1c3670);border-radius:10px 18px 6px 6px}
.ad-banner .ad-tag{position:absolute;right:14px;top:6px;font:700 11px "Arimo",sans-serif;color:var(--navy)}
.ad-banner .ad-cta{position:absolute;right:8px;bottom:8px;border:1px solid #555;padding:3px 10px;font-size:10px;color:#333}

/* articles */
.section-title{left:85px;top:1630px;color:var(--navy);font-size:20px;font-weight:600}
.carousel-btn{top:1632px;width:20px;height:20px;background:#888}
.carousel-btn svg{display:block}
.article-img{left:85px;width:232px;height:158px}
.article-title{left:343px;color:var(--navy);font-size:14.5px;font-weight:600}
.article-author{left:338px;display:flex;align-items:center;gap:10px;font-size:13px;color:#444}
.avatar{width:34px;height:34px;border-radius:50%;background:linear-gradient(#b98a6a,#6e4f3a)}
.article-text{left:343px;width:470px;font-size:12.5px;line-height:25px;color:#555}
.read-more{left:343px;font-size:13px;color:var(--navy);text-decoration:underline}
.divider{left:85px;width:731px;height:1px;background:var(--line)}

/* sidebar */
.side-ad{left:833px;top:1636px;width:280px;height:234px;background:linear-gradient(160deg,#1b1d1f,#3a3d40 55%,#1f4a2d)}
.side-feature{left:833px;width:280px}
.side-icon{position:absolute;left:0;top:0;width:65px;height:58px;background:linear-gradient(135deg,#8aa3c2,#3b5a85)}
.side-feature h4{position:absolute;left:80px;top:0;font-size:12px;font-weight:700;color:#333}
.side-feature p{position:absolute;left:80px;top:26px;width:200px;font-size:12.5px;line-height:23px;color:#555}

/* footer */
.footer-bg{left:0;top:2463px;width:1200px;height:251px;background:var(--footer-bg)}
.footer h3{position:absolute;color:var(--navy);font-size:16px;font-weight:600}
.footer ul{position:absolute;list-style:none}
.footer li{height:27.5px;font-size:13px;color:#333;position:relative;padding-left:31px}
.footer li::before{content:"»";position:absolute;left:0;top:-2px;color:#333;font-size:14px}
.news-text{position:absolute;left:864px;top:2535px;width:250px;font-size:12.5px;line-height:23px;color:#444}
.news-input{position:absolute;left:864px;top:2595px;width:245px;height:37px;border:1px solid #ccc;background:var(--white);font-size:12.5px;color:#555;padding:11px 12px}
.news-submit{position:absolute;left:864px;top:2643px;width:93px;height:32px;background:var(--blue);color:var(--white);font:700 13px "Montserrat",sans-serif;text-align:center;line-height:32px}

.bottom-bar{left:0;top:2714px;width:1200px;height:68px;background:var(--navy-deep)}
.copyright{left:85px;top:2740px;color:var(--white);font-size:13px}
.social{top:2729px;width:38px;height:38px;border-radius:50%;border:2px solid var(--white)}
</style>
</head>
<body>

<header class="abs site-header">
  <div class="abs brand"><span class="brand-mark"></span>CoinHarbor.com</div>
  <nav class="abs nav">
    <a class="active" style="left:0">HOME</a>
    <a style="left:72px">ANNUITIES</a>
    <a style="left:172px">AUTO INSURANCE</a>
    <a style="left:311px">CREDIT MONITORING</a>
    <a style="left:467px">DEBT MANAGEMENT</a>
    <a style="left:621px">MORTGAGES</a>
  </nav>
  <div class="abs search-btn">
    <svg width="44" height="44" viewBox="0 0 44 44"><circle cx="21" cy="21" r="5" fill="none" stroke="#fff" stroke-width="2"/><line x1="25" y1="25" x2="28" y2="28" stroke="#fff" stroke-width="2.4" stroke-linecap="round"/></svg>
  </div>
</header>

<section>
  <div class="abs hero" role="img" aria-label="Person working on a laptop with a calculator and financial papers"></div>
  <div class="abs hero-shade"></div>
  <h1 class="abs hero-title">MAKE SMARTER FINANCIAL DECISIONS</h1>
  <p class="abs hero-sub">FIND THE BEST FINANCIAL PRODUCTS &amp; SERVICES</p>
  <div class="abs hero-search"><span>I'm looking for Product or Category</span><b>SEARCH</b></div>
</section>

<h2 class="abs welcome-title">WELCOME TO COINHARBOR</h2>
<p class="abs welcome-text">Parents, let’s face it – the high cost of raising children leaves us all needing a little extra money. Short of getting a big raise</p>

<section>
  <div class="abs tile" style="left:85px;top:744px;width:369px;height:213px;background:linear-gradient(135deg,#9aa4ad,#4a5561)" role="img" aria-label="Car key handover with silver car"><span class="tile-label">AUTO INSURANCE</span></div>
  <div class="abs tile" style="left:458px;top:744px;width:217px;height:213px;background:linear-gradient(135deg,#b59a86,#6f5a4d)" role="img" aria-label="Hands holding a credit card"><span class="tile-label">CREDIT MONITORING</span></div>
  <div class="abs tile" style="left:677px;top:744px;width:217px;height:213px;background:linear-gradient(135deg,#6c6f73,#3b3d41)" role="img" aria-label="Laptop on desk with paperwork"><span class="tile-label">CREDIT REPAIR</span></div>
  <div class="abs tile" style="left:896px;top:744px;width:217px;height:293px;background:linear-gradient(135deg,#6d7378,#2c3135)" role="img" aria-label="Hands using a smartphone"><span class="tile-label">DEBT MANAGEMENT</span></div>

  <div class="abs tile" style="left:85px;top:959px;width:217px;height:213px;background:linear-gradient(135deg,#7c8896,#3f4a58)" role="img" aria-label="Credit card with a padlock"><span class="tile-label">IDENTITY THEFT</span></div>
  <div class="abs tile tile-feature" style="left:306px;top:959px;width:586px;height:291px" role="img" aria-label="Calculator and documents in blue tint">
    <h3 class="feature-title">STUDENT LOAN CONSOLIDATION</h3>
    <p class="feature-text">Most people already have budgets that are extremely stretched, therefor it is not surprising that most people want to spend the least amount they possibly can on car insurance.</p>
  </div>
  <div class="abs tile" style="left:896px;top:1039px;width:217px;height:211px;background:linear-gradient(135deg,#4d5a70,#1f2a3e)" role="img" aria-label="Student studying with notebook"><span class="tile-label">PAYDAY LOANS</span></div>

  <div class="abs tile" style="left:85px;top:1176px;width:217px;height:289px;background:linear-gradient(135deg,#9e8a7a,#5a4b40)" role="img" aria-label="Hands passing a set of keys"><span class="tile-label">ONLINE BROKERAGES</span></div>
  <div class="abs tile" style="left:306px;top:1254px;width:271px;height:211px;background:linear-gradient(135deg,#c2b9ae,#8a8075)" role="img" aria-label="Senior couple at home"><span class="tile-label">LIFE INSURANCE</span></div>
  <div class="abs tile" style="left:581px;top:1254px;width:267px;height:211px;background:linear-gradient(135deg,#b89c82,#6d5846)" role="img" aria-label="Signing financial documents"><span class="tile-label">PERSONAL FINANCE</span></div>
  <div class="abs tile" style="left:851px;top:1254px;width:262px;height:211px;background:linear-gradient(135deg,#8c97a5,#4a5466)" role="img" aria-label="Advisor meeting with a couple"><span class="tile-label">TAX SETTLEMENT</span></div>
</section>

<aside class="abs ad-banner">
  <span class="ad-tag">Drive On</span>
  <div class="ad-head">ALL-NEW VANTRA ROAMER</div>
  <div class="ad-sub">123PS Power Engine</div>
  <div class="ad-car" role="img" aria-label="Blue compact SUV"></div>
  <span class="ad-cta">EXPLORE NOW</span>
</aside>

<h2 class="abs section-title">RECENT ARTICLES</h2>
<div class="abs carousel-btn" style="left:772px"><svg width="20" height="20"><path d="M12 6 L8 10 L12 14" fill="none" stroke="#fff" stroke-width="2"/></svg></div>
<div class="abs carousel-btn" style="left:794px"><svg width="20" height="20"><path d="M8 6 L12 10 L8 14" fill="none" stroke="#fff" stroke-width="2"/></svg></div>

<article>
  <div class="abs article-img" style="top:1690px;background:linear-gradient(135deg,#d8c4a8,#8b7157)" role="img" aria-label="Stacks of coins"></div>
  <h3 class="abs article-title" style="top:1690px">5 “EASY” WAYS PARENTS CAN SAVE</h3>
  <div class="abs article-author" style="top:1724px"><span class="avatar"></span>by Dale Morrow</div>
  <p class="abs article-text" style="top:1775px">Parents, let’s face it – the high cost of raising children leaves us all needing a little extra money.Short of getting a big raise, switching jobs, or winning the lottery, earning “more you can’t make more save dollars every year.</p>
  <a class="abs read-more" style="top:1866px">Read more...</a>
</article>
<div class="abs divider" style="top:1901px"></div>

<article>
  <div class="abs article-img" style="top:1951px;background:linear-gradient(135deg,#e8dcae,#7a7360)" role="img" aria-label="Person standing in a sunlit office"></div>
  <h3 class="abs article-title" style="top:1951px">MOTORCYCLE INSURANCE BASICS</h3>
  <div class="abs article-author" style="top:1985px"><span class="avatar"></span>by Dale Morrow</div>
  <p class="abs article-text" style="top:2036px">Parents, let’s face it – the high cost of raising children leaves us all needing a little extra money.Short of getting a big raise, switching jobs, or winning the lottery, earning “more you can’t make more save dollars every year.</p>
  <a class="abs read-more" style="top:2127px">Read more...</a>
</article>
<div class="abs divider" style="top:2178px"></div>

<article>
  <div class="abs article-img" style="top:2217px;background:linear-gradient(135deg,#e4e0da,#9aa3ad)" role="img" aria-label="Advisor meeting with clients at a desk"></div>
  <h3 class="abs article-title" style="top:2217px">HOW DO I GET CHEAP AUTO INSURANCE?</h3>
  <div class="abs article-author" style="top:2251px"><span class="avatar"></span>by Dale Morrow</div>
  <p class="abs article-text" style="top:2302px">Parents, let’s face it – the high cost of raising children leaves us all needing a little extra money.Short of getting a big raise, switching jobs, or winning the lottery, earning “more you can’t make more save dollars every year.</p>
  <a class="abs read-more" style="top:2393px">Read more...</a>
</article>

<aside>
  <div class="abs side-ad" role="img" aria-label="Advertisement with a green sports convertible"></div>
  <div class="abs side-feature" style="top:1905px">
    <div class="side-icon" role="img" aria-label="Team analyzing charts"></div>
    <h4>WE ANALYZE &amp; EXPLAIN</h4>
    <p>We analyze &amp; explain how each online service works</p>
  </div>
  <div class="abs side-feature" style="top:1995px">
    <div class="side-icon" role="img" aria-label="People comparing services"></div>
    <h4>WE TEST &amp; COMPARE</h4>
    <p>We test &amp; compare the leading services in each category</p>
  </div>
  <div class="abs side-feature" style="top:2090px">
    <div class="side-icon" role="img" aria-label="Hand holding a phone"></div>
    <h4>WE REVIEW &amp; RATE</h4>
    <p>We review and rate each service to show which is best</p>
  </div>
</aside>

<footer class="footer">
  <div class="abs footer-bg"></div>
  <h3 style="left:85px;top:2492px">ALL SERVICES REVIEWED</h3>
  <ul style="left:85px;top:2540px">
    <li>Annuities</li><li>Auto Insurance</li><li>Credit Monitoring</li><li>Credit Repair</li><li>Debt Management</li>
  </ul>
  <ul style="left:270px;top:2540px">
    <li>Homeowners Insurance</li><li>Identity Theft</li><li>Life Insuranc</li><li>eMortgages</li><li>Online Brokerage</li>
  </ul>
  <ul style="left:457px;top:2540px">
    <li>Payday Loans</li><li>Personal Finance</li><li>Student Loan Consolidation</li><li>Tax Settlement</li>
  </ul>
  <h3 style="left:667px;top:2492px">SERVICES REVIEWED</h3>
  <ul style="left:667px;top:2540px">
    <li>Debt Management</li><li>Payday Loans</li><li>Credit Cards</li>
  </ul>
  <h3 style="left:864px;top:2492px">NEWSLETTER</h3>
  <p class="news-text">Subscribe To Our Newsletter To Get The Latest Great Deals And Reviews</p>
  <div class="news-input">Enter Your email :</div>
  <div class="news-submit">SUBMIT</div>

  <div class="abs bottom-bar"></div>
  <p class="abs copyright">Copyright © 2017 CoinHarbor. All rights reserved.</p>
  <span class="abs social" style="left:903px"></span>
  <span class="abs social" style="left:946px"></span>
  <span class="abs social" style="left:990px"></span>
  <span class="abs social" style="left:1033px"></span>
  <span class="abs social" style="left:1075px"></span>
</footer>

</body>
</html>
```